Transform Your Giving

I need a tri-fold brochure that will fit in a standard number 10 business envelope. Meadowlark and Allied Services is a charitable nonprofit. The goal of this brochure is to stimulate people into thinking about other ways to make a donation. The design should communicate the essential information on donation options, create a sense of professional integrity, be graphically sharp, easy to read and laid out in a way that doesn't make the material appear crowded.

```html
<!DOCTYPE html>
<html lang="en">
<head>
<meta charset="utf-8">
<title>Transform Your Giving – Meadowlark and Allied Services</title>
<link href="https://fonts.googleapis.com/css2?family=Poppins:ital,wght@0,400;0,500;0,600;0,700;0,800;1,500;1,600&display=swap" rel="stylesheet">
<style>
:root{
  --navy:#2e2a7c;
  --green:#46b649;
  --ink:#2b2b2b;
  --backdrop:#cfcfcf;
  --white:#ffffff;
}
*{box-sizing:border-box;margin:0;padding:0}
html,body{width:800px;height:1200px;overflow:hidden;background:var(--backdrop);font-family:'Poppins',sans-serif;color:var(--ink)}
.sheet{position:absolute;left:66px;width:669px;height:518px;background:var(--white);overflow:hidden}
.sheet-outside{top:67px}
.sheet-inside{top:615px}
.panel{position:absolute;top:0;width:223px;height:518px}
.abs{position:absolute}
.p1{left:0}.p2{left:223px}.p3{left:446px}
.navy-bg{background:var(--navy)}
.h-green{color:var(--green)}
.body{font-size:7px;line-height:8.2px;text-align:justify}
.title{font-weight:700;font-size:8.2px;line-height:9.6px;color:var(--navy)}
.title .g{color:var(--green);display:block}
.lead{font-style:italic;font-weight:600;font-size:7px;line-height:8.3px}
.how{font-weight:700;font-size:10px;color:var(--navy)}
.how span{color:var(--green)}
.ring{position:absolute;border-radius:50%;background:var(--white);display:flex;align-items:center;justify-content:center}
.ring.navy{border:2px solid var(--navy)}
.ring.green{border:2px solid var(--green)}
.photo{position:absolute}
.brand{text-align:center}
.brand .mark{display:inline-flex;align-items:center;gap:4px;font-weight:800;color:var(--navy);letter-spacing:1px}
.brand .mark i{display:inline-block;border-radius:50%;background:var(--green)}
.brand .legal{font-weight:700;color:var(--navy);letter-spacing:.3px}
.url{font-weight:500;letter-spacing:2px;color:var(--ink)}
.url b{color:var(--green);font-weight:600}
.giving-list{position:absolute;left:31px;top:121px;width:164px;height:128px;border:1px solid var(--green);border-radius:4px}
.giving-item{position:absolute;display:flex;align-items:center;gap:6px;font-size:8.8px;font-weight:600;color:var(--ink)}
.giving-item .ring{position:relative;width:19px;height:19px}
.dash{position:absolute;border-top:1px dashed #9a9a9a}
.bullet{position:absolute;display:flex;gap:5px;font-size:7px;line-height:8.2px}
.bullet .tick{flex:0 0 6px;height:6px;margin-top:1px;border-radius:50%;background:var(--green)}
.intro-lines{position:absolute;right:23px;top:31px;text-align:right;font-size:6.6px;line-height:8.2px;white-space:nowrap}
</style>
</head>
<body>

<section class="sheet sheet-outside">

  <div class="panel p1">
    <h2 class="abs" style="left:25px;top:26px;font-size:11.5px;font-weight:800;color:var(--navy)">THE IMPACT <span class="h-green">OF</span> YOUR GIFT</h2>
    <p class="abs body" style="left:25px;top:47px;width:172px;font-size:7.6px;line-height:9.1px">Your generosity drives our mission. With every Smart gift you’re supporting Meadowlark and Allied Services. Join our community of Smart Givers today and make an enduring impact. With Smart Giving your generosity reaches further. Begin your Smart Giving journey with us today.</p>
    <div class="giving-list">
      <div class="giving-item" style="top:8px;left:-7px"><span class="ring navy"><svg width="10" height="10" viewBox="0 0 10 10"><circle cx="5" cy="5" r="4" fill="none" stroke="#2e2a7c" stroke-width="1"/><text x="5" y="7.2" font-size="6" text-anchor="middle" fill="#2e2a7c" font-family="Poppins">c</text></svg></span>Crypto</div>
      <div class="giving-item" style="top:30px;left:-7px"><span class="ring green"><svg width="10" height="10" viewBox="0 0 10 10"><path d="M1 4h8L5 1z M2 5v3M4 5v3M6 5v3M8 5v3M1 9h8" stroke="#777" fill="none" stroke-width=".8"/></svg></span>DAF’s</div>
      <div class="giving-item" style="top:52px;left:-7px"><span class="ring navy"><svg width="10" height="10" viewBox="0 0 10 10"><path d="M2 9V6M4 9V4M6 9V5M8 9V2" stroke="#777" stroke-width="1"/></svg></span>Stocks &amp; Securities</div>
      <div class="giving-item" style="top:75px;left:-7px"><span class="ring navy"><svg width="10" height="10" viewBox="0 0 10 10"><rect x="1.5" y="4" width="7" height="5" fill="none" stroke="#777" stroke-width=".8"/><path d="M1 3h8v1H1zM5 3v6" stroke="#777" stroke-width=".8" fill="none"/></svg></span>QCDs</div>
      <div class="giving-item" style="top:98px;left:-7px"><span class="ring green"><svg width="10" height="10" viewBox="0 0 10 10"><path d="M1 5l2 3h4l2-3M5 2v4" stroke="#777" stroke-width=".8" fill="none"/></svg></span>Charitable Annuity</div>
    </div>
    <div class="photo" role="img" aria-label="Photo of a smiling couple packing clothes into a donations box" style="left:0;top:255px;width:223px;height:263px;background:linear-gradient(180deg,#f4f4f4 0%,#d9e3e6 30%,#9fbcc0 55%,#c9a98a 85%,#d8c0a0 100%)"></div>
  </div>

  <div class="panel p2 navy-bg">
    <div class="brand abs" style="left:0;top:30px;width:223px">
      <div class="mark" style="font-size:24px;color:var(--white)"><i style="width:8px;height:8px"></i>MAAS</div>
      <div class="legal" style="font-size:4.3px;color:var(--white)">MEADOWLARK AND ALLIED SERVICES, INC.</div>
    </div>
    <p class="abs" style="left:28px;top:87px;width:167px;text-align:center;font-size:7.6px;line-height:9.1px;font-weight:700;color:var(--white)"><span class="h-green">To learn more about Smart Giving Options and how they can benefit you and</span> Meadowlark and Allied Services, please reach out to our team. We’re here to help you navigate these giving methods and answer any question you may have.</p>
    <div class="abs" style="left:102px;top:158px;font-size:22px;font-weight:800;color:var(--green);line-height:20px">“</div>
    <div class="abs" style="left:26px;top:167px;width:171px;height:44px;border:1px solid var(--green);border-radius:5px;overflow:hidden">
      <p style="padding:5px 8px 0;text-align:center;font-size:7.4px;font-style:italic;color:var(--white);line-height:8.6px">Being kind to others is a way of being good to yourself.</p>
      <div style="position:absolute;left:0;bottom:0;width:100%;height:15px;background:var(--green);color:var(--white);font-weight:700;font-size:8.5px;text-align:center;line-height:15px">RUTH CALLOWAY</div>
    </div>
    <p class="abs" style="left:0;top:223px;width:223px;text-align:center;font-size:8px;color:var(--white)">If you do not have a will, go to</p>
    <div class="abs" style="left:28px;top:237px;width:168px;height:16px;border:1px solid var(--green);border-radius:8px;text-align:center;font-size:11px;font-weight:700;color:var(--green);line-height:15px;letter-spacing:.5px">www.EasyWillPlan.com</div>
    <p class="abs" style="left:36px;top:256px;width:151px;text-align:center;font-size:8px;line-height:9.6px;color:var(--white)">In 20 minutes you can have a legal will – for free</p>

    <div class="abs" style="left:17px;top:286px;width:190px;height:232px;background:var(--green);border-radius:6px 6px 0 0">
      <div class="abs" style="left:35px;top:0;width:120px;height:22px;background:var(--white);border-radius:0 0 14px 14px;text-align:center;font-size:13.5px;font-weight:800;color:var(--navy);line-height:22px">CONTACT US</div>
      <p class="abs" style="left:0;top:28px;width:190px;text-align:center;font-size:11px;font-weight:800;color:var(--navy)">HAVE MORE QUESTION?</p>
      <p class="abs" style="left:25px;top:43px;width:140px;text-align:center;font-size:7.4px;line-height:8.8px;color:var(--navy)">Please contact us at Meadowlark and Allied Services</p>
      <svg class="abs" style="left:89px;top:66px" width="12" height="12" viewBox="0 0 12 12"><circle cx="6" cy="6" r="6" fill="#2e2a7c"/><path d="M4 3.5c0 2.5 2 4.5 4.5 4.5l.5-1-1.2-.7-.6.6c-.8-.4-1.4-1-1.8-1.8l.6-.6L5.3 3z" fill="#fff"/></svg>
      <p class="abs" style="left:0;top:80px;width:190px;text-align:center;font-size:7.4px;color:var(--ink)">555-014-2260(ext. 100)</p>
      <svg class="abs" style="left:89px;top:90px" width="12" height="12" viewBox="0 0 12 12"><circle cx="6" cy="6" r="6" fill="#2e2a7c"/><rect x="3" y="4" width="6" height="4" fill="#fff"/><path d="M3 4l3 2.2L9 4" stroke="#2e2a7c" stroke-width=".7" fill="none"/></svg>
      <p class="abs" style="left:0;top:103px;width:190px;text-align:center;font-size:7.4px;color:var(--ink)">rlarsen@maasinc.org</p>
      <svg class="abs" style="left:89px;top:114px" width="12" height="12" viewBox="0 0 12 12"><circle cx="6" cy="6" r="6" fill="#2e2a7c"/><path d="M6 9.5L4 6a2 2 0 114 0z" fill="#fff"/><circle cx="6" cy="5.6" r=".8" fill="#2e2a7c"/></svg>
      <p class="abs" style="left:0;top:128px;width:190px;text-align:center;font-size:7.4px;color:var(--ink)">1420 Prairie Rd. Suite 8 Fairview, ND&nbsp; 58000</p>
      <svg class="abs" style="left:89px;top:138px" width="12" height="12" viewBox="0 0 12 12"><circle cx="6" cy="6" r="6" fill="#2e2a7c"/><circle cx="6" cy="6" r="3" fill="none" stroke="#fff" stroke-width=".7"/><path d="M3 6h6M6 3v6" stroke="#fff" stroke-width=".6"/></svg>
      <p class="abs" style="left:0;top:151px;width:190px;text-align:center;font-size:7.4px;color:var(--ink)">www.maasinc.org</p>
      <p class="abs" style="left:21px;top:168px;font-size:8.6px;color:var(--ink)">Follow us</p>
      <div class="dash" style="left:65px;top:176px;width:101px;border-color:#555"></div>
      <p class="abs" style="left:10px;top:181px;width:170px;text-align:center;font-size:4.7px;line-height:6px;color:var(--navy)">This material has been prepared for informational purposes only and is not intended to provide tax, accounting, or legal advice. Meadowlark and Allied Services is not a professional fiduciary organization. Please consult with your tax advisor or financial professional before making a decision about Smart Giving</p>
    </div>
  </div>

  <div class="panel p3">
    <h1 class="abs" style="left:0;top:22px;width:223px;text-align:center;font-size:20px;line-height:21px;font-weight:800;color:var(--navy)">TRANSFORM<br><span class="h-green">YOUR GIVING</span></h1>
    <div class="abs" style="left:27px;top:73px;width:170px;border-top:1px solid #bbb"></div>
    <div class="abs" style="left:88px;top:71px;width:46px;height:4px;border-radius:2px;background:var(--green)"></div>
    <h2 class="abs" style="left:0;top:83px;width:223px;text-align:center;font-size:25px;line-height:26px;font-weight:800;color:var(--navy)">BE STRATEGIC<br>BE SMART</h2>
    <p class="abs" style="left:18px;top:142px;width:187px;text-align:center;font-size:11.2px;line-height:13px;color:var(--ink)">Discover the impact of Smart Giving with Meadowlark and Allied Services</p>
    <div class="photo" role="img" aria-label="Illustration framing a photo of an older couple embracing over green hills, with small giving icons around it" style="left:0;top:196px;width:223px;height:206px;background:linear-gradient(180deg,#ffffff 0%,#c6d0da 35%,#8fa3b3 60%,#5f7d55 82%,#46653f 100%)"></div>
    <svg class="abs" style="left:0;top:392px" width="223" height="24" viewBox="0 0 223 24">
      <path d="M0 14Q111 -6 223 14V24H0z" fill="#46b649"/>
      <path d="M0 20Q111 2 223 20V24H0z" fill="#ffffff"/>
    </svg>
    <div class="brand abs" style="left:0;top:418px;width:223px">
      <div class="mark" style="font-size:24px"><i style="width:8px;height:8px"></i>MAAS</div>
      <div class="legal" style="font-size:4.3px">MEADOWLARK AND ALLIED SERVICES, INC.</div>
    </div>
    <p class="abs url" style="left:0;top:473px;width:223px;text-align:center;font-size:14px">www.<b>maasinc</b>.org</p>
  </div>
</section>

<section class="sheet sheet-inside">

  <div class="panel p1">
    <svg class="abs" style="left:0;top:0" width="80" height="80" viewBox="0 0 80 80"><path d="M0 0H80L0 80z" fill="#2e2a7c"/></svg>
    <p class="intro-lines">We would like to introduce you to five<br>Strategic and Smart ways to give that could<br>potentially be more beneficial to you compared<br>to traditional cash donations.</p>
    <p class="abs" style="left:25px;top:74px;width:175px;font-size:7px;line-height:8.2px">We encourage you to keep this information as a guide for your future contributions.</p>
    <span class="ring navy" style="left:25px;top:98px;width:31px;height:31px"><svg width="14" height="14" viewBox="0 0 14 14"><path d="M2 12V9M5 12V7M8 12V8M11 12V4" stroke="#777" stroke-width="1.2"/></svg></span>
    <h3 class="abs title" style="left:61px;top:97px;width:160px">GIFTS OF STOCKS OR APPRECIATED <span class="g">ASSETS STRATEGIC &amp; SMART</span></h3>
    <p class="abs lead" style="left:61px;top:121px;width:140px">Consider your long-term publicly traded stock as a way to give to your favorite charity.</p>
    <p class="abs body" style="left:25px;top:147px;width:176px">You can make a significantly bigger impact when you donate long-term appreciated securities, including stock, mutual funds, and bonds, directly to your favorite charity.</p>
    <h4 class="abs how" style="left:25px;top:189px">HOW DOES <span>IT WORK?</span></h4>
    <p class="abs body" style="left:25px;top:205px;width:174px">When you donate stock to a charity, you will generally take a tax deduction for the full market value. Because you are donating stock, your contribution and tax deduction may be significantly higher than contributing the after-tax proceeds. The same benefits apply when you donate mutual funds or bonds.</p>
    <div class="photo" role="img" aria-label="Photo of two young volunteers packing food into donation bags and boxes" style="left:0;top:279px;width:223px;height:239px;background:linear-gradient(180deg,#ffffff 0%,#efe8e2 25%,#d8c4b0 55%,#c9ab85 80%,#e8e2da 100%)"></div>
  </div>

  <div class="panel p2">
    <span class="ring green" style="left:17px;top:29px;width:31px;height:31px"><svg width="14" height="14" viewBox="0 0 14 14"><path d="M1 5h12L7 1z M3 6v5M5.5 6v5M8.5 6v5M11 6v5M1 12.5h12" stroke="#777" fill="none" stroke-width="1"/></svg></span>
    <h3 class="abs title" style="left:55px;top:31px;width:160px">DONOR-ADVISED FUND (DAF) <span class="g">STRATEGIC &amp; SMART</span></h3>
    <p class="abs lead" style="left:55px;top:54px;width:140px">Consider a DAF – a simple, flexible, and tax-advantageous way to give to your favorite charities.</p>
    <p class="abs" style="left:17px;top:87px;width:165px;font-size:7.6px;line-height:9px">A Donor-Advised Fund (DAF), is like a charitable investment account for the sole purpose of supporting your favorite charities.</p>
    <h4 class="abs how" style="left:17px;top:133px">HOW DOES <span>IT WORK?</span></h4>
    <p class="abs body" style="left:17px;top:150px;width:180px">You establish a DAF and contribute cash, stocks, or non-publicly traded assets, cryptocurrency, and private company stock to be eligible for an immediate tax deduction. Those funds are contributed for tax-free growth. You can recommend grants be made from your DAF to any IRS qualified public charity</p>
    <div class="dash" style="left:17px;top:227px;width:172px"></div>
    <span class="ring green" style="left:17px;top:243px;width:31px;height:31px"><svg width="14" height="14" viewBox="0 0 14 14"><rect x="2" y="6" width="10" height="7" fill="none" stroke="#777" stroke-width="1"/><path d="M1 4h12v2H1zM7 4v9" stroke="#777" stroke-width="1" fill="none"/></svg></span>
    <h3 class="abs title" style="left:55px;top:242px;width:150px">QUALIFIED CHARITABLE <span class="g">DISTRIBUTIONS (QCDS) STRATEGIC &amp; SMART</span></h3>
    <p class="abs lead" style="left:55px;top:274px;width:148px">Consider a QCD – when planning your IRA withdrawal strategy…and donate to your favorite charity.</p>
    <p class="abs body" style="left:14px;top:307px;width:186px">IRA owners at age 70 ½ or over can transfer dollars from their IRA to charity tax-free each year. These transfers known as Qualified Charitable Distributions (QCDs) offer eligible older Americans a great way to easily give to charity.</p>
    <h4 class="abs how" style="left:14px;top:361px">HOW DOES <span>IT WORK?</span></h4>
    <p class="abs body" style="left:14px;top:377px;width:186px"><b>Are you 72 and required to take a minimum distribution (RMD) from your IRA but do not need the funds?</b> Consider a Qualified Charitable Distribution. Normally, distributions from a traditional IRA are taxable when received. With a QCD, these distributions become tax-free when paid directly from the IRA to your favorite eligible charity. An IRA owner wishing to make a QCD should contact their IRA trustee, allowing time to complete the transaction before the end of the year to receive the tax benefit.</p>
    <p class="abs url" style="left:0;top:478px;width:223px;text-align:center;font-size:10px">www.<b>maasinc</b>.org</p>
  </div>

  <div class="panel p3">
    <span class="ring navy" style="left:15px;top:28px;width:31px;height:31px"><svg width="14" height="14" viewBox="0 0 14 14"><circle cx="7" cy="7" r="5.5" fill="none" stroke="#777" stroke-width="1"/><text x="7" y="10" font-size="8" text-anchor="middle" fill="#777" font-family="Poppins">c</text></svg></span>
    <h3 class="abs title" style="left:52px;top:27px;width:160px">CRYPTOCURRENCY <span class="g">STRATEGIC &amp; SMART</span></h3>
    <p class="abs lead" style="left:52px;top:49px;width:160px">Consider donating Bitcoin and other cryptocurrencies to your favorite charity.</p>
    <p class="abs body" style="left:15px;top:73px;width:184px">Bitcoin and other cryptocurrencies can be donated to charity just like other appreciated assets such as stocks and other business interests. Before you sell bitcoin and donate the after-tax proceeds, consider donating your bitcoin directly to a favorite charity.</p>
    <h4 class="abs how" style="left:15px;top:120px">HOW DOES <span>IT WORK?</span></h4>
    <p class="abs body" style="left:15px;top:135px;width:184px">Many donors find it useful to open a Donor-Advised Fund (DAF). This strategy includes two significant benefits, both for you and your favorite charity.</p>
    <div class="bullet" style="left:16px;top:167px;width:184px"><span class="tick"></span><span>Your tax deduction will be equal to the fair market value of the donated bitcoin (as determined by a qualified appraisal).</span></div>
    <div class="bullet" style="left:16px;top:198px;width:184px"><span class="tick"></span><span>Your cryptocurrency donation is tax-smart because it may eliminate capital gains on the value / appreciation AND your favorite charity will receive 100% of the value of the contribution.</span></div>
    <p class="abs body" style="left:16px;top:235px;width:182px">Often charities are not able to accept direct donations of bitcoin/crypto so using a DAF is a great way to donate these assets.</p>
    <div class="dash" style="left:15px;top:267px;width:182px"></div>
    <span class="ring navy" style="left:17px;top:285px;width:31px;height:31px"><svg width="14" height="14" viewBox="0 0 14 14"><path d="M1 7l3 5h6l3-5M7 2v6" stroke="#777" stroke-width="1" fill="none"/><circle cx="7" cy="4" r="2" fill="none" stroke="#777" stroke-width=".8"/></svg></span>
    <h3 class="abs title" style="left:53px;top:286px;width:160px">CHARITABLE GIFT ANNUITY <span class="g">STRATEGIC &amp; SMART</span></h3>
    <p class="abs lead" style="left:53px;top:307px;width:140px">Consider establishing a Charitable Gift Annuity</p>
    <p class="abs body" style="left:17px;top:327px;width:182px;text-align:left">You make a donation to a single charity. The gift is set aside in a reserve account and invested.</p>
    <h4 class="abs how" style="left:17px;top:351px">HOW DOES <span>IT WORK?</span></h4>
    <p class="abs body" style="left:17px;top:366px;width:182px">A charitable gift annuity is a contract between a donor and a charity. As a donor, you make a sizable gift to charity using cash, securities, or possibly other assets. This money is then invested. In return, you become eligible to take a partial tax deduction for your donation, plus you receive a fixed stream of income from the charity for the rest of your life. At the end of your life (as well as your spouse’s, if you’re giving as a couple), the charity receives the remainder of the gift.</p>
    <svg class="abs" style="left:131px;top:430px" width="92" height="88" viewBox="0 0 92 88"><path d="M92 0V88H0z" fill="#46b649"/></svg>
    <div class="brand abs" style="left:0;top:452px;width:170px">
      <div class="mark" style="font-size:19px"><i style="width:6px;height:6px"></i>MAAS</div>
      <div class="legal" style="font-size:3.6px">MEADOWLARK AND ALLIED SERVICES, INC.</div>
    </div>
  </div>
</section>

</body>
</html>
```